Professional violinist needs business cards

I am trying to attract the following jobs:
-private violin lessons (primarily classical)
-performance gigs (weddings, birthday parties, funerals, etc.)
-collaborations with other artists (studio recordings, performances)

I want to communicate that I have a very high standard of excellence for my work, but I also love people and celebrations.
Values/style words I like are:
love, joy, peace, fun, beauty, authenticity, excellence, warmth, refined/sleek, free spirited. If that's too confusing, just ignore :)

I will attach my favorite business card template that I could find on Canva. The lines are supposed to be like a music staff, which I think is really cool, but I also don't want it to look too busy. I like the simple black and white--I think it looks sharp--but I also am open to other ideas. I also have seen business cards with pictures included that looked great, so I attached an image that could be used as well.

I am also attaching a file that I made of my initials that could be used as a logo, but I'm not sure if it should be included.

Information on the card:
-My name (18 letters total)
-"violinist"
-phone number, email, website

Thank you!

```html
<!DOCTYPE html>
<html lang="en">
<head>
<meta charset="utf-8">
<title>Elena Marlowe – Violinist Business Card</title>
<link rel="stylesheet" href="https://fonts.googleapis.com/css2?family=Urbanist:wght@400;700&family=Open+Sans:wght@400;700&display=swap">
<style>
  :root{
    --page:#1c1c1d;
    --card-shadow:rgba(0,0,0,.55);
    --white:#ffffff;
    --soft-white:#e9e6e2;
    --muted:#cfcac4;
    --icon-bg:#8c8c8c;
    --band:rgba(0,0,0,.5);
    --stone-1:#7d7462;
    --stone-2:#4b453a;
    --stone-3:#2a2722;
    --wood-1:#2b1d16;
    --wood-2:#140d0a;
    --violin:#6e3a1f;
  }
  *{box-sizing:border-box;margin:0;padding:0}
  html,body{width:1200px;height:1108px;overflow:hidden}
  body{background:var(--page);position:relative}

  .card{
    position:absolute;top:204px;width:420px;height:700px;
    border-radius:22px;overflow:hidden;
    box-shadow:0 18px 40px var(--card-shadow);
  }
  .card--front{left:150px}
  .card--back{left:630px}

  /* front */
  .front-photo{
    position:absolute;inset:0;
    background:
      radial-gradient(ellipse 38% 55% at 52% 48%, #121010 0%, rgba(18,16,16,.85) 45%, transparent 75%),
      linear-gradient(160deg,var(--stone-1) 0%,var(--stone-2) 55%,var(--stone-3) 100%);
  }
  .front-band{
    position:absolute;left:0;right:0;top:330px;bottom:0;
    background:var(--band);
  }
  .front-info{
    position:absolute;left:0;right:0;top:372px;
    text-align:center;color:var(--white);
    font-family:"Urbanist",sans-serif;
  }
  .person-name{font-weight:700;font-size:30px;letter-spacing:.5px;text-transform:uppercase;line-height:1}
  .person-role{font-weight:400;font-size:24px;margin-top:4px;color:var(--soft-white)}
  .rule{height:1px;background:var(--soft-white);opacity:.8;margin:0 auto}
  .rule--top{width:250px;margin-top:22px}
  .icons{display:flex;justify-content:center;gap:8px;margin-top:-14px}
  .icon{width:30px;height:30px;border-radius:5px;background:var(--icon-bg);display:flex;align-items:center;justify-content:center}
  .contact{margin-top:16px;font-size:22px;line-height:1.3;color:var(--white)}
  .rule--bottom{width:250px;margin-top:16px}

  /* back */
  .back-photo{
    position:absolute;inset:0;
    background:
      radial-gradient(ellipse 30% 40% at 68% 68%, var(--violin) 0%, rgba(110,58,31,.35) 50%, transparent 80%),
      linear-gradient(170deg,var(--wood-1) 0%,var(--wood-2) 70%,#070505 100%);
  }
  .brand{
    position:absolute;left:0;right:0;top:120px;
    display:flex;align-items:center;justify-content:center;gap:12px;
    font-family:"Open Sans",sans-serif;font-weight:700;font-size:30px;color:var(--muted);
  }
  .brand-dot{width:16px;height:16px;border-radius:50%;background:var(--muted)}
  .services{
    position:absolute;left:44px;right:30px;top:420px;
    font-family:"Open Sans",sans-serif;color:var(--muted);list-style:none;
  }
  .service{margin-bottom:20px}
  .service-title{font-weight:700;font-size:23px;line-height:1.2}
  .service-note{font-weight:400;font-size:19px;line-height:1.3}
</style>
</head>
<body>

<section class="card card--front">
  <div class="front-photo" role="img" aria-label="Photo of the violinist in a black dress holding her violin and bow beside a stone wall and stair railing"></div>
  <div class="front-band"></div>
  <div class="front-info">
    <h1 class="person-name">Elena Marlowe</h1>
    <p class="person-role">Managing Director</p>
    <div class="rule rule--top"></div>
    <div class="icons">
      <span class="icon" aria-label="phone">
        <svg width="18" height="18" viewBox="0 0 24 24"><path fill="#fff" d="M6.6 10.8a15 15 0 0 0 6.6 6.6l2.2-2.2c.3-.3.7-.4 1-.2 1.1.4 2.3.6 3.6.6.6 0 1 .4 1 1V20c0 .6-.4 1-1 1A17 17 0 0 1 3 4c0-.6.4-1 1-1h3.5c.6 0 1 .4 1 1 0 1.3.2 2.5.6 3.6.1.3 0 .7-.2 1z"/></svg>
      </span>
      <span class="icon" aria-label="email">
        <svg width="18" height="18" viewBox="0 0 24 24"><rect x="3" y="6" width="18" height="12" fill="none" stroke="#fff" stroke-width="2"/><path d="M3 6l9 7 9-7" fill="none" stroke="#fff" stroke-width="2"/></svg>
      </span>
      <span class="icon" aria-label="website">
        <svg width="18" height="18" viewBox="0 0 24 24"><circle cx="12" cy="12" r="9" fill="none" stroke="#fff" stroke-width="2"/><path d="M3 12h18M12 3c3 3 3 15 0 18M12 3c-3 3-3 15 0 18" fill="none" stroke="#fff" stroke-width="1.5"/></svg>
      </span>
    </div>
    <div class="contact">
      <p>044-987 654 321</p>
      <p>hello@marlowestrings.com</p>
      <p>www.marlowestrings.com</p>
    </div>
    <div class="rule rule--bottom"></div>
  </div>
</section>

<section class="card card--back">
  <div class="back-photo" role="img" aria-label="Photo of a violin and bow resting against a dark wooden background"></div>
  <div class="brand"><span class="brand-dot"></span>Marlowe Strings</div>
  <ul class="services">
    <li class="service">
      <p class="service-title">Private violin lessons</p>
      <p class="service-note">(primarily classical)</p>
    </li>
    <li class="service">
      <p class="service-title">Performance gigs</p>
      <p class="service-note">(weddings, birthday parties, funerals, etc.)</p>
    </li>
    <li class="service">
      <p class="service-title">Collaborations with other artists</p>
      <p class="service-note">(studio recordings, performances)</p>
    </li>
  </ul>
</section>

</body>
</html>
```